Private Investment Firm Needs PowerPoint Presentation Template

Design PowerPoint template, take Pinebrook-submitted rough presentation draft, and drop it into new template. See attached Project Brief file for more detail.
Updates

Some decent designs have been submitted but they seem to lack the understanding of our target markets. I am hopeful that more time and feedback will result in better results.

Target Market(s)

Private company owners and intermediaries.

Font styles to use
Serif

Colors
3176b5

Requirements
Must have
• See attached Project Brief.
Nice to have
Should not have
• No B2C fluff--this is a B2B project.

```html
<!DOCTYPE html>
<html lang="en">
<head>
<meta charset="utf-8">
<title>Pinebrook Capital — Presentation Template</title>
<link rel="stylesheet" href="https://fonts.googleapis.com/css2?family=Cormorant+SC:wght@500;600;700&family=Montserrat:wght@300;400;500;600;700&display=swap">
<style>
:root{
  --brand-blue:#3176b5;
  --deep-blue:#1565b8;
  --navy:#0d3f78;
  --sky:#5bc8ec;
  --slate:#555a60;
  --ink:#3c3f44;
  --muted:#6b7077;
  --paper:#ffffff;
  --paper-shade:#eceef1;
  --backdrop:#ecebe8;
}
*{margin:0;padding:0;box-sizing:border-box}
html,body{width:1200px;height:1200px;overflow:hidden;background:var(--backdrop)}
body{position:relative;font-family:"Montserrat",sans-serif;color:var(--ink)}
.slide{position:absolute;width:460px;height:258px;overflow:hidden;
  background:linear-gradient(120deg,var(--paper-shade) 0%,var(--paper) 45%,var(--paper) 60%,var(--paper-shade) 100%);
  box-shadow:0 4px 12px rgba(0,0,0,.22)}
.slide-frame{position:absolute;inset:0;width:100%;height:100%}
.abs{position:absolute}
.center{left:0;right:0;text-align:center}
.serif-sc{font-family:"Cormorant SC",serif;font-weight:700}
.brand{display:flex;align-items:center;gap:5px;justify-content:center;
  font-family:"Cormorant SC",serif;font-weight:700;color:var(--navy);letter-spacing:.08em}
.brand .dot{border-radius:50%;background:var(--brand-blue)}
.web{font-size:8px;color:var(--ink)}
.web b{color:var(--deep-blue);font-weight:600}
.date-box{border:1px solid #9aa0a6;background:#fff;font-weight:300;color:var(--ink);text-align:center}
.page-num{font-size:5.5px;color:#fff;font-weight:600}

/* cover */
.cover-title{top:52px;font-size:25px;line-height:25px;color:var(--deep-blue);letter-spacing:.02em}
.cover-sub{top:110px;font-size:6.5px;line-height:9.5px;color:var(--muted)}
.cover-sub b{color:var(--deep-blue);font-weight:600}

/* intro */
.section-head{font-size:14px;font-weight:700;color:var(--deep-blue);letter-spacing:.04em}
.bullets{left:58px;width:300px;top:72px;list-style:none;font-size:6.8px;line-height:8.2px;color:var(--ink)}
.bullets li{position:relative;padding-left:12px;margin-bottom:9px}
.bullets li::before{content:"";position:absolute;left:0;top:2px;width:2.5px;height:2.5px;border-radius:50%;background:var(--deep-blue)}
.bullets .ticks{list-style:none;margin-top:3px}
.bullets .ticks li{margin:0 0 3px 10px;padding-left:9px}
.bullets .ticks li::before{content:"✓";background:none;width:auto;height:auto;top:0;font-size:6px;color:var(--deep-blue)}

/* questionnaire */
.q-title{top:16px;font-size:9.5px;font-weight:600;color:var(--ink)}
.q-banner-text{font-size:11px;line-height:13px;font-family:"Cormorant SC",serif;font-weight:600;color:#fff}
.q-tag{top:77px;font-size:8px;font-weight:700}
.q-col{top:94px;font-size:4px;line-height:5px}
.q-item{position:relative;padding-left:14px;margin-bottom:6px}
.q-num{position:absolute;left:0;top:0;width:9px;height:9px;border-radius:50%;background:var(--deep-blue);color:#fff;font-size:5px;font-weight:700;display:flex;align-items:center;justify-content:center}
.q-q{font-weight:700;color:var(--ink)}
.q-a{margin-top:3px;color:var(--muted)}
.q-a b{color:var(--deep-blue)}
.q-note{margin-top:3px;color:var(--muted)}

/* epilogue */
.epi-title{top:58px;font-size:34px;line-height:38px;font-weight:300;letter-spacing:.06em;color:var(--ink)}
.epi-rule{left:209px;top:103px;width:42px;height:3px;background:var(--deep-blue)}

/* capital stack */
.stack-col{left:52px;width:103px}
.stack-head{height:12px;background:var(--deep-blue);color:#fff;font-size:7px;font-weight:700;display:flex;align-items:center;justify-content:center}
.stack-row{height:13px;border-bottom:1px solid #fff;background:linear-gradient(#f3f4f6,#d9dcdf);font-size:4.5px;display:flex;align-items:center;justify-content:center;color:var(--ink)}
.stack-box{left:158px;width:229px;color:#fff;font-size:5px;line-height:6px;text-align:center;display:flex;flex-direction:column;justify-content:center;padding:0 12px}
.stack-box b{font-weight:700;margin-bottom:1px}
.stack-divider{left:52px;top:159px;width:335px;height:3px;
  background:repeating-linear-gradient(90deg,var(--navy) 0 50px,var(--sky) 50px 70px)}

/* contact */
.contact-list{left:38px;top:58px;width:220px}
.contact-line{left:42px;top:60px;width:1px;height:160px;background:#c9ccd0}
.contact-item{position:relative;padding-left:20px;margin-bottom:14px;font-size:7.5px;line-height:8.8px;color:var(--ink)}
.contact-item::before{content:"";position:absolute;left:2px;top:1px;width:5px;height:5px;border-radius:50%;background:#fff;border:1.5px solid var(--slate)}
.contact-item h4{font-size:7.5px;font-weight:700;color:var(--deep-blue)}
.contact-item .tel{color:var(--deep-blue)}
.contact-item b{color:var(--deep-blue);font-weight:600}
.portrait{left:332px;top:99px;width:100px;height:100px;border-radius:50%;border:3px solid #fff;
  background:radial-gradient(circle at 50% 40%,#dfe6ee 0%,#b9c6d4 55%,#2f3b4d 100%);box-shadow:0 2px 6px rgba(0,0,0,.25)}
</style>
</head>
<body>

<!-- Cover -->
<section class="slide" style="left:426px;top:36px">
  <svg class="slide-frame" viewBox="0 0 460 258" preserveAspectRatio="none">
    <polygon points="0,0 46,0 6,210 0,210" fill="#555a60"/>
    <polygon points="446,0 460,0 460,258 366,258" fill="#1565b8"/>
  </svg>
  <h1 class="abs center cover-title serif-sc">Introduction to<br>Non-Control Capital</h1>
  <p class="abs center cover-sub">The Lower Middle Market Private Company Strategy for<br>Raising Capital While <b>Maintaining Business Control</b></p>
  <div class="abs date-box" style="left:177px;top:148px;width:106px;height:28px;font-size:17px;line-height:26px">14.11.2018</div>
  <div class="abs center brand" style="top:198px;font-size:11px"><span class="dot" style="width:12px;height:12px"></span>Pinebrook Capital</div>
  <p class="abs center web" style="top:239px;font-size:9px">www.<b>pinebrookcapital</b>.com</p>
</section>

<!-- Introduction -->
<section class="slide" style="left:119px;top:331px">
  <svg class="slide-frame" viewBox="0 0 460 258" preserveAspectRatio="none">
    <polygon points="0,0 46,0 6,210 0,210" fill="#555a60"/>
    <polygon points="446,0 460,0 460,258 366,258" fill="#1565b8"/>
  </svg>
  <h2 class="abs section-head" style="left:152px;top:30px">INTRODUCTION</h2>
  <ul class="abs bullets">
    <li>Private company owners have traditionally considered two capital raising options
      <ul class="ticks">
        <li>Borrow from a local bank, or</li>
        <li>Sell most or all of the company to a change-of-control investor (aka Buyout firm)</li>
      </ul>
    </li>
    <li>An alternative most have not considered is the raising of Non-Control Capital, or capital that is invested into the business yet allows those same owners to retain controlling interest in their company</li>
    <li>Non-Control Capital is not appropriate for every private company owner but neither is a Change-of-Control sale</li>
    <li>The key is to determine what the business and owners require, and then partner with an investor best aligned with those needs so that long-term company growth, and personal goals, can both be achieved</li>
  </ul>
  <div class="abs brand" style="top:208px;left:210px;font-size:7px"><span class="dot" style="width:9px;height:9px"></span>Pinebrook Capital</div>
  <p class="abs web" style="left:206px;top:230px;font-size:7px">www.<b>pinebrookcapital</b>.com</p>
  <p class="abs page-num" style="left:432px;top:243px">1.</p>
</section>

<!-- Questionnaire -->
<section class="slide" style="left:630px;top:334px">
  <svg class="slide-frame" viewBox="0 0 460 258" preserveAspectRatio="none">
    <polygon points="0,0 46,0 6,210 0,210" fill="#555a60"/>
    <polygon points="446,0 460,0 460,258 366,258" fill="#1565b8"/>
    <polygon points="52,32 60,32 50,70 42,70" fill="#555a60"/>
    <polygon points="64,32 395,32 386,70 55,70" fill="#1565b8"/>
    <polygon points="399,32 424,32 415,70 390,70" fill="#555a60"/>
    <polygon points="185,77 189,77 186,89 182,89" fill="#555a60"/>
    <polygon points="192,77 265,77 262,89 189,89" fill="#0d3f78"/>
    <polygon points="268,77 272,77 269,89 265,89" fill="#555a60"/>
  </svg>
  <h3 class="abs center q-title">Non-Control Capital Questionnaire</h3>
  <p class="abs center q-banner-text" style="top:38px">The Critical Questions to Ask of<br>Any Prospective Non-Control Investor</p>
  <p class="abs q-tag" style="color:#fff;text-align:center;left:190px;width:74px;line-height:12px">Questions</p>
  <div class="abs q-col" style="left:26px;width:186px">
    <div class="q-item"><span class="q-num">1</span>
      <p class="q-q">How many years has the firm been investing Non-Control Capital?</p>
      <p class="q-a"><b>Best Answer:</b> 5+ years investing as a team within the current firm</p>
      <p class="q-note">Shows shared judgment in evaluating and making NCC investments, raising the likelihood of closing</p></div>
    <div class="q-item"><span class="q-num">2</span>
      <p class="q-q">How many fully-invested Non-Control Capital funds in the firm's history?</p>
      <p class="q-a"><b>Best Answer:</b> 2+ fully-invested funds</p>
      <p class="q-note">Shows skill closing deals with the current approach; firms without it may only be testing the waters</p></div>
    <div class="q-item"><span class="q-num">3</span>
      <p class="q-q">What percentage of the firm's voting investment committee are full-time Non-Control Capital investors?</p>
      <p class="q-a"><b>Best Answer:</b> Super-majority. Shows commitment, experience and focus on NCC</p></div>
    <div class="q-item"><span class="q-num">4</span>
      <p class="q-q">What is the number of Non-Control Capital investments made with the current firm and team?</p>
      <p class="q-a"><b>Best Answer:</b> 20+ shows long-term experience with current team and process</p></div>
  </div>
  <div class="abs q-col" style="left:228px;width:150px">
    <div class="q-item"><span class="q-num">5</span>
      <p class="q-q">What percentage of portfolio investments made are "sponsorless" (those without a change-of-control investor)?</p>
      <p class="q-a"><b>Best Answer:</b> 80%+ of all investments closed in the last 5 years</p>
      <p class="q-note">Shows ability to add value as a sole minority investor, not simply as a back-up to another sponsor</p></div>
    <div class="q-item"><span class="q-num">6</span>
      <p class="q-q">Can the investor show quantifiable proof of their ability to assist portfolio companies with growth and improvement?</p>
      <p class="q-a"><b>Best Answer:</b> Yes. Owners should review actual revenue, EBITDA and employee growth results over time</p>
      <p class="q-note">Shows true value-added ability to help owners grow their businesses</p></div>
  </div>
  <div class="abs brand" style="left:300px;top:222px;font-size:7px"><span class="dot" style="width:9px;height:9px"></span>Pinebrook</div>
  <p class="abs web" style="left:40px;top:237px;font-size:7px">www.<b>pinebrookcapital</b>.com</p>
  <p class="abs page-num" style="left:432px;top:244px">2.</p>
</section>

<!-- Epilogue -->
<section class="slide" style="left:426px;top:622px">
  <svg class="slide-frame" viewBox="0 0 460 258" preserveAspectRatio="none">
    <polygon points="0,0 46,0 6,210 0,210" fill="#555a60"/>
    <polygon points="446,0 460,0 460,258 366,258" fill="#1565b8"/>
  </svg>
  <h2 class="abs center epi-title">EPILOGUE</h2>
  <div class="abs epi-rule"></div>
  <div class="abs date-box" style="left:178px;top:120px;width:104px;height:27px;font-size:17px;line-height:25px">14.11.2018</div>
  <div class="abs center brand" style="top:165px;font-size:12px"><span class="dot" style="width:13px;height:13px"></span>Pinebrook Capital</div>
  <p class="abs center web" style="top:211px;font-size:11px">www.<b>pinebrookcapital</b>.com</p>
</section>

<!-- Capital stack -->
<section class="slide" style="left:110px;top:910px">
  <svg class="slide-frame" viewBox="0 0 460 258" preserveAspectRatio="none">
    <polygon points="0,0 46,0 6,210 0,210" fill="#555a60"/>
    <polygon points="446,0 460,0 460,258 366,258" fill="#1565b8"/>
    <polygon points="68,22 76,22 68,47 60,47" fill="#555a60"/>
    <polygon points="80,22 388,22 380,47 72,47" fill="#1565b8"/>
    <polygon points="392,22 400,22 392,47 384,47" fill="#555a60"/>
  </svg>
  <h2 class="abs serif-sc" style="left:82px;top:25px;width:300px;text-align:center;font-size:15px;color:#fff;font-weight:600">Pinebrook Provides Junior Capital</h2>
  <div class="abs" style="left:52px;top:53px;width:335px;height:12px;background:var(--sky);font-size:7.5px;font-weight:700;color:var(--navy);text-align:center;line-height:12px">Balance Sheet Seniority / Capital Stack Hierarchy</div>
  <div class="abs stack-col" style="top:74px">
    <div class="stack-head">Senior Debt</div>
    <div class="stack-row">Revolver</div>
    <div class="stack-row">Asset-Based Loan</div>
    <div class="stack-row">Senior Term Loan</div>
    <div class="stack-head">Combination</div>
    <div class="stack-row">Unitranche</div>
  </div>
  <div class="abs stack-box" style="top:74px;height:78px;background:var(--navy)">
    <b>Senior Debt Capital Providers</b>
    Paid back first, plays more of a lender than partner role, less value-added, less equity dilutive, less expensive capital, but not strategically focused
  </div>
  <div class="abs stack-divider"></div>
  <div class="abs stack-col" style="top:167px">
    <div class="stack-head">Junior Capital</div>
    <div class="stack-row">Subordinated Debt</div>
    <div class="stack-row">Preferred Stock</div>
    <div class="stack-row">Common Stock</div>
  </div>
  <div class="abs stack-box" style="top:167px;height:52px;background:#0a2d5c">
    <b>What Pinebrook Invests</b>
    Sits junior to all other capital (taking on more risk), plays a partner role, more value-added services provided, more expensive than senior debt, but supplies an engine for continuous improvement and growth
  </div>
  <div class="abs brand" style="left:309px;top:225px;font-size:7px"><span class="dot" style="width:9px;height:9px"></span>Pinebrook</div>
  <p class="abs web" style="left:52px;top:242px;font-size:7px">www.<b>pinebrookcapital</b>.com</p>
  <p class="abs page-num" style="left:432px;top:243px">3.</p>
</section>

<!-- Contact -->
<section class="slide" style="left:628px;top:912px">
  <svg class="slide-frame" viewBox="0 0 460 258" preserveAspectRatio="none">
    <polygon points="0,0 46,0 6,210 0,210" fill="#555a60"/>
    <polygon points="446,0 460,0 460,258 366,258" fill="#1565b8"/>
    <polygon points="166,16 172,16 167,34 161,34" fill="#555a60"/>
    <polygon points="175,16 290,16 285,34 170,34" fill="#1565b8"/>
    <polygon points="293,16 299,16 294,34 288,34" fill="#555a60"/>
  </svg>
  <h2 class="abs" style="left:172px;top:17px;width:116px;text-align:center;font-size:13px;font-weight:400;color:#fff;letter-spacing:.05em">CONTACT</h2>
  <div class="abs contact-line"></div>
  <div class="abs contact-list">
    <div class="contact-item">
      <h4>Daniel R. Hollis</h4>
      Principal<br>41 Harbor Ridge Road, Suite 210<br>Milford, CT 06460<br>Direct: (555) 210-4471<br>dhollis@<b>pinebrookcapital</b>.com
    </div>
    <div class="contact-item">
      <h4>Northeast Office</h4>
      18 Millpond Way, Suite 300<br>Andover, MA 01810<br><span class="tel">(555) 210-4400</span>
    </div>
    <div class="contact-item">
      <h4>West Coast Office</h4>
      220 Bay Terrace, Suite 500<br>Oakland, CA 94607<br><span class="tel">(555) 388-1900</span>
    </div>
  </div>
  <div class="abs portrait" role="img" aria-label="Portrait photo of the firm's principal"></div>
  <div class="abs brand" style="left:274px;top:224px;font-size:7px"><span class="dot" style="width:9px;height:9px"></span>Pinebrook</div>
  <p class="abs web" style="left:43px;top:240px;font-size:7px">www.<b>pinebrookcapital</b>.com</p>
  <p class="abs page-num" style="left:432px;top:243px">4.</p>
</section>

</body>
</html>
```